Black Car Limousine transportation business in Naples Florida

Always stand for my reliability and RVD stands for Love, K and M are the first initials of my children's names. It should show professionalism and a dedication to customer service. We keep our clients identities private. Show our professionalism. We are Black car Black tie company. We service transportation on a reserve basis to and from residents, airports, casinos, hotels,

Target Market(s)

It is a Private car service. High end clients. Businesses, Celebrity and athletes. Service to airports, hotels, special events.

Industry/Entity Type

Business

Contact Information for Business Card

A pearl metallic or Luster card. Standard business card size. Would like the name, Company email, show we take credit cards and phone number. Currently I don't have a website but will like to add later.

Logo Text

STEADFAST RVD TRANSPORTATION

Font styles to use
Serif

Colors
eaeaea
000000

Requirements
Must have
• Must have Company email, show we take credit cards and phone number. Currently I don't have a website but will like to add later.
Nice to have
• Would like to stay with a black and white theme. Open to some color trim.
Should not have
• Open to suggestions

```html
<!DOCTYPE html>
<html lang="en">
<head>
<meta charset="utf-8">
<title>Steadfast RVD Transportation – Business Card</title>
<link rel="stylesheet" href="https://fonts.googleapis.com/css2?family=Cormorant+Garamond:wght@400;500;600&display=swap">
<style>
  :root {
    --backdrop: #d9d6d0;
    --card-black: #0b0b0b;
    --card-black-edge: #1c1c1c;
    --card-pearl: #eaeaea;
    --card-pearl-light: #f7f7f7;
    --ink-white: #ffffff;
    --ink-black: #111111;
    --ink-grey: #5e5e5e;
    --rule-grey: #555555;
  }
  * { box-sizing: border-box; margin: 0; padding: 0; }
  html, body {
    width: 771px;
    height: 1200px;
    overflow: hidden;
    background: var(--backdrop);
    font-family: "Cormorant Garamond", Georgia, serif;
  }
  .sheet { position: relative; width: 771px; height: 1200px; }
  .card {
    position: absolute;
    left: 85px;
    width: 600px;
    height: 343px;
    border-radius: 4px;
    box-shadow: 0 10px 24px rgba(0,0,0,0.25);
    overflow: hidden;
  }
  .card-front {
    top: 150px;
    background: linear-gradient(160deg, var(--card-black-edge) 0%, var(--card-black) 55%, #000 100%);
    color: var(--ink-white);
  }
  .front-brand {
    position: absolute;
    left: 0; right: 0;
    top: 110px;
    display: flex;
    flex-direction: column;
    align-items: center;
  }
  .brand-mark { display: flex; align-items: center; gap: 12px; }
  .brand-square { width: 22px; height: 22px; background: currentColor; flex: none; }
  .brand-name {
    font-weight: 500;
    font-size: 26px;
    letter-spacing: 2px;
    line-height: 1;
    text-transform: uppercase;
    white-space: nowrap;
  }
  .brand-tagline {
    margin-top: 16px;
    font-weight: 500;
    font-size: 36px;
    letter-spacing: 0.5px;
    line-height: 1;
  }
  .card-back {
    top: 707px;
    background: linear-gradient(150deg, var(--card-pearl-light) 0%, var(--card-pearl) 70%, #e0e0e0 100%);
    color: var(--ink-black);
  }
  .back-brand {
    position: absolute;
    right: 36px;
    top: 40px;
    display: flex;
    flex-direction: column;
    align-items: flex-end;
  }
  .back-brand .brand-name { font-size: 19px; letter-spacing: 1.5px; }
  .back-brand .brand-square { width: 16px; height: 16px; }
  .back-brand .brand-tagline { margin-top: 10px; font-size: 28px; }
  .holder {
    position: absolute;
    left: 36px;
    top: 160px;
    padding-left: 14px;
    border-left: 6px solid var(--rule-grey);
  }
  .holder-name { font-size: 28px; font-weight: 500; line-height: 1.05; }
  .holder-title { font-size: 16px; font-weight: 400; color: var(--ink-grey); margin-top: 2px; }
  .contact-list {
    position: absolute;
    left: 270px;
    bottom: 30px;
    list-style: none;
    font-size: 17px;
    font-weight: 500;
    color: var(--ink-grey);
  }
  .contact-list li { display: flex; align-items: center; gap: 8px; margin-top: 5px; }
  .contact-icon { width: 14px; height: 14px; fill: var(--ink-grey); }
  .card-icons { display: flex; gap: 6px; }
  .card-icon { width: 26px; height: 17px; }
  .card-icon rect.body { fill: none; stroke: var(--ink-grey); stroke-width: 1.4; }
  .card-icon rect.stripe { fill: var(--ink-grey); }
</style>
</head>
<body>
<main class="sheet">
  <section class="card card-front" aria-label="Card front">
    <div class="front-brand">
      <div class="brand-mark">
        <span class="brand-square"></span>
        <span class="brand-name">Steadfast RVD Transportation</span>
      </div>
      <p class="brand-tagline">Limousine Services</p>
    </div>
  </section>

  <section class="card card-back" aria-label="Card back">
    <div class="back-brand">
      <div class="brand-mark">
        <span class="brand-square"></span>
        <span class="brand-name">Steadfast RVD Transportation</span>
      </div>
      <p class="brand-tagline">Limousine Services</p>
    </div>

    <div class="holder">
      <p class="holder-name">Your Name</p>
      <p class="holder-title">Job Title</p>
    </div>

    <ul class="contact-list">
      <li>
        <svg class="contact-icon" viewBox="0 0 16 16" aria-hidden="true">
          <path d="M2 5c0-1.5 2.5-3 6-3s6 1.5 6 3v1.5h-3.5V5h-5v1.5H2z"/>
          <rect x="3" y="8" width="10" height="6" rx="1"/>
        </svg>
        <span>000 000 0000</span>
      </li>
      <li>
        <svg class="contact-icon" viewBox="0 0 16 16" aria-hidden="true">
          <path d="M1 3h14v1.2L8 9 1 4.2z"/>
          <path d="M1 5.6l7 4.9 7-4.9V13H1z"/>
        </svg>
        <span>youremail@xyz.com</span>
      </li>
      <li class="card-icons" role="img" aria-label="Credit cards accepted">
        <svg class="card-icon" viewBox="0 0 26 17" aria-hidden="true">
          <rect class="body" x="1" y="1" width="24" height="15" rx="2"/>
          <rect class="stripe" x="1" y="4" width="24" height="3"/>
        </svg>
        <svg class="card-icon" viewBox="0 0 26 17" aria-hidden="true">
          <rect class="body" x="1" y="1" width="24" height="15" rx="2"/>
          <rect class="stripe" x="4" y="10" width="8" height="2"/>
        </svg>
        <svg class="card-icon" viewBox="0 0 26 17" aria-hidden="true">
          <rect class="body" x="1" y="1" width="24" height="15" rx="2"/>
          <rect class="stripe" x="1" y="4" width="24" height="3"/>
        </svg>
      </li>
    </ul>
  </section>
</main>
</body>
</html>
```